Verdant Systems Business Card

want the back of card to be blue- with the logo in the center
front of card- info plus logo (info being mailing address, email address, and website address )
4 different names with titles to have on cards
1) Calvin Borsted - Owner
2) Naomi Trelvik- Customer Relationship Specialist
3) Felix Andrade- Vice President of Sales
4) Owen Markby- Chief Technology Officer

Target Market(s)

tech company in the government/probation office industry

Industry/Entity Type

Government Office

Contact Information for Business Card

1) Calvin Borsted - Owner

Colors
0355a3
ffffff

Requirements
Must have
• back side should be blue, with the logo placed in the center
• front side needs to include both the logo, as well as company info (info should include website address, email address, and mailing address)

```html
<!DOCTYPE html>
<html lang="en">
<head>
<meta charset="utf-8">
<title>Verdant Systems Business Card</title>
<link href="https://fonts.googleapis.com/css2?family=Noto+Serif:wght@400;600&family=Roboto:wght@400&display=swap" rel="stylesheet">
<style>
  :root {
    --navy: #27386a;
    --white: #ffffff;
    --paper: #f7f7f7;
    --swoosh: #8e8e99;
    --ink-grey: #6a6a6a;
    --backdrop: #a9a7a8;
  }
  html, body {
    margin: 0;
    width: 1200px;
    height: 1200px;
    overflow: hidden;
    background: var(--backdrop);
  }
  .canvas {
    position: relative;
    width: 1200px;
    height: 1200px;
  }
  .card {
    position: absolute;
    border-radius: 22px;
    overflow: hidden;
  }
  .card-back {
    left: 238px;
    top: 118px;
    width: 714px;
    height: 420px;
    background: var(--navy);
    display: flex;
    align-items: center;
    justify-content: center;
  }
  .brand-name {
    font-family: "Noto Serif", serif;
    font-weight: 600;
    text-transform: uppercase;
    white-space: nowrap;
    margin: 0;
  }
  .card-back .brand-name {
    color: var(--white);
    font-size: 52px;
    letter-spacing: 1px;
  }
  .card-front {
    left: 230px;
    top: 644px;
    width: 717px;
    height: 416px;
    background: var(--paper);
  }
  .wave {
    position: absolute;
    left: 0;
    top: 0;
  }
  .person {
    position: absolute;
    right: 34px;
    top: 30px;
    text-align: right;
    color: var(--white);
  }
  .person-name {
    font-family: "Noto Serif", serif;
    font-weight: 400;
    font-size: 24px;
    letter-spacing: 0.5px;
    margin: 0 0 6px;
  }
  .person-title {
    font-family: "Roboto", sans-serif;
    font-size: 17px;
    line-height: 23px;
    margin: 0;
  }
  .card-front .brand-name {
    position: absolute;
    left: 36px;
    top: 208px;
    color: var(--navy);
    font-size: 38px;
  }
  .address {
    position: absolute;
    left: 33px;
    top: 330px;
    font-family: "Roboto", sans-serif;
    font-size: 17px;
    line-height: 25px;
    color: var(--ink-grey);
    margin: 0;
    font-style: normal;
  }
  .contacts {
    position: absolute;
    right: 32px;
    top: 305px;
    margin: 0;
    padding: 0;
    list-style: none;
    font-family: "Roboto", sans-serif;
    font-size: 17px;
    line-height: 26px;
    color: var(--ink-grey);
    text-align: right;
  }
  .contacts li {
    display: flex;
    align-items: center;
    justify-content: flex-end;
    gap: 10px;
  }
  .contact-icon {
    width: 14px;
    height: 14px;
    fill: var(--navy);
  }
</style>
</head>
<body>
<div class="canvas">

  <section class="card card-back" aria-label="Card back">
    <p class="brand-name">Verdant Systems</p>
  </section>

  <section class="card card-front" aria-label="Card front">
    <svg class="wave" width="717" height="416" viewBox="0 0 717 416" aria-hidden="true">
      <path d="M0,0 H717 V110 C640,128 560,160 470,152 C360,142 250,42 0,40 Z" fill="var(--navy)"/>
      <path d="M0,40 C250,42 360,142 470,152 C560,160 640,128 717,110 V124 C640,145 560,175 470,168 C360,158 250,58 0,56 Z" fill="var(--swoosh)"/>
      <path d="M60,72 C180,44 300,38 420,50 C300,46 180,56 60,76 Z" fill="var(--swoosh)"/>
    </svg>

    <div class="person">
      <p class="person-name">NAOMI TRELVIK</p>
      <p class="person-title">Customer Relationship<br>Specialist</p>
    </div>

    <p class="brand-name">Verdant Systems</p>

    <address class="address">234 Anywhere St., Any City,<br>Any Town, US 123456</address>

    <ul class="contacts">
      <li>111-111-1111
        <svg class="contact-icon" viewBox="0 0 16 16" aria-hidden="true"><path d="M1 5c0-2 3-3 7-3s7 1 7 3v2h-4V5H5v2H1z M3 8h10l1 6H2z"/></svg>
      </li>
      <li>www.verdantsystems.com
        <svg class="contact-icon" viewBox="0 0 16 16" aria-hidden="true"><path d="M1 3h14v10H1z M2 4l6 5 6-5" stroke="var(--white)" stroke-width="1"/></svg>
      </li>
      <li>naomi.t@verdantsystems.com
        <svg class="contact-icon" viewBox="0 0 16 16" aria-hidden="true"><circle cx="8" cy="8" r="7"/><path d="M1 8h14 M8 1v14 M8 1c-4 4-4 10 0 14 M8 1c4 4 4 10 0 14" stroke="var(--white)" stroke-width="0.9" fill="none"/></svg>
      </li>
    </ul>
  </section>

</div>
</body>
</html>
```